Fire Risk Assessment App needs a sleek UI design

I need a sleek, modern but professional design for my 5 page Fire Risk Assessment App. Include gradient background, fire themed colours including reds, yellows, light orange and a touch of black. Design must ooze simplicity and professionalism. This is for the UK market. See attached images and word doc for more information.

Target Market(s)

General public and business owners

Industry/Entity Type

Technology / Fire Safety

Colors
00AB8E
00BBA5
67D7C9
C6EFE9
E9F9F6
59FF00
82FF00
B8FF75
E3FFCB
F4FFEA
FFC000
F8CF3A
FAE287
FDF2CF
FEFAEE
F0912C
F2A743
F7CA91
FBE8D2
FDF5EE
EE7325
F08F49
F5BC92
FAE3D3
FDF4ED
EB3D1F
EC4F4E
F09395
F8D3D4
FCEDEE

```html
<!DOCTYPE html>
<html lang="en">
<head>
<meta charset="utf-8">
<title>Fire Risk Assessment App – Screens</title>
<link href="https://fonts.googleapis.com/css2?family=Poppins:wght@400;500;600&display=swap" rel="stylesheet">
<style>
:root{
  --page:#f4f2f0;
  --fire-dark:#2e0604;
  --fire-mid:#7c0c08;
  --fire-red:#b3100b;
  --fire-bright:#c9150e;
  --gold-top:#f8cf3a;
  --gold-bottom:#e8b44a;
  --green:#0bbf00;
  --white:#ffffff;
  --ink:#2a1a10;
  --nav-active:#6e0a07;
  --muted:#6b6b6b;
}
*{box-sizing:border-box;margin:0;padding:0}
html,body{width:1200px;height:697px;overflow:hidden}
body{background:var(--page);font-family:"Poppins",sans-serif;position:relative}
.screen{position:absolute;top:83px;width:254px;height:531px;overflow:hidden;
  background:linear-gradient(180deg,var(--fire-dark) 0%,var(--fire-mid) 30%,var(--fire-red) 70%,var(--fire-bright) 100%);
  box-shadow:0 12px 30px rgba(0,0,0,.28);color:var(--white)}
.screen--welcome{left:128px}
.screen--dashboard{left:473px}
.screen--support{left:819px}
.abs{position:absolute}
.headline{left:0;right:0;top:22px;text-align:center;font-size:18.5px;line-height:25px;font-weight:500}
.doc-art{left:51px;top:119px;width:131px;height:114px;border-radius:6px;
  background:linear-gradient(135deg,#f4efe9,#d8cfc6 60%,#8a4a22);transform:rotate(-8deg);opacity:.95}
.field{left:17px;width:220px;height:29px;background:var(--white);border-radius:3px;color:#777;font-size:8.5px;display:flex;align-items:center;padding-left:10px}
.mic{position:absolute;border-radius:50%;background:#c8110c;display:flex;align-items:center;justify-content:center}
.btn-gold{background:linear-gradient(180deg,var(--gold-top),var(--gold-bottom));color:var(--ink);border-radius:3px;display:flex;align-items:center;justify-content:center}
.btn-create{left:17px;top:320px;width:220px;height:29px;font-size:10px;font-weight:500}
.tagline{left:0;right:0;top:364px;text-align:center;font-size:10.5px}
.btn-login{left:17px;top:397px;width:220px;height:29px;border:1.2px solid var(--white);background:#9e0c08;border-radius:3px;display:flex;align-items:center;justify-content:center;font-size:10px;font-weight:600}
.btn-icon{position:absolute;left:22px;top:6px}
.finger{left:108px;top:452px;width:38px;height:41px}
.credit{left:0;right:0;top:503px;text-align:center;font-size:8.3px}
.gauge{left:15px;top:26px;width:38px;height:38px;border-radius:50%;background:var(--white);border:2px solid #ddd}
.plus{left:105px;top:24px;width:44px;height:44px;border-radius:50%;background:#c8110c;display:flex;align-items:center;justify-content:center}
.start-box{left:82px;top:77px;width:90px;height:15px;border:1px dashed #e9c9c5;font-size:6.6px;display:flex;align-items:center;justify-content:center}
.tile{top:105px;width:35px;height:32px;border-radius:3px;border:1px solid #ddd}
.tile--commercial{left:64px;background:linear-gradient(180deg,#6f8fc8,#2b3f6e)}
.tile--residential{left:152px;background:linear-gradient(180deg,#e9ebe8,#7b8579)}
.tile-label{top:140px;font-size:8.5px;color:#f1d9d6;width:70px;text-align:center}
.complete{left:13px;top:184px;width:228px;height:25px;background:var(--green);border-radius:2px;font-size:9px;font-weight:600;display:flex;align-items:center;padding-left:10px}
.complete .tick{position:absolute;right:8px;top:4px}
.site-link{left:0;right:0;top:222px;text-align:center;font-size:8.8px;display:flex;justify-content:center;align-items:center;gap:4px}
.section-bar{left:12px;width:230px;height:25px;font-size:8.8px}
.radio-row{left:19px;font-size:8.6px;display:flex;align-items:center;gap:6px}
.radio{width:10px;height:10px;border-radius:50%;border:1px solid var(--white);display:inline-flex;align-items:center;justify-content:center}
.radio--on::after{content:"";width:5px;height:5px;border-radius:50%;background:var(--white)}
.nav{left:0;top:483px;width:254px;height:48px;background:var(--white);border-radius:22px 22px 0 0}
.nav-pill{position:absolute;top:1px;height:47px;background:var(--nav-active);border-radius:24px 24px 0 24px}
.nav-item{position:absolute;top:8px;width:60px;margin-left:-30px;text-align:center;font-size:7px;color:var(--muted)}
.nav-item--active{color:var(--white)}
.nav-item svg{display:block;margin:0 auto 4px}
.support-icon{left:15px;top:33px}
.support-title{left:60px;right:0;top:35px;text-align:center;font-size:13.5px}
.prompt{left:19px;top:82px;font-size:9.5px}
.textbox{left:20px;top:108px;width:216px;height:97px;background:var(--white);border-radius:3px;color:#333;font-size:7.3px;padding:9px 9px}
.btn-send{left:17px;top:214px;width:219px;height:29px;font-size:10px;font-weight:600}
.btn-send svg{position:absolute;right:10px;top:7px}
</style>
</head>
<body>

<section class="screen screen--welcome">
  <h1 class="abs headline">The most user friendly<br>Fire Risk Assessment<br>App Available.</h1>
  <div class="abs doc-art" role="img" aria-label="Illustration of fire risk assessment question sheets with a photo of firefighters"></div>
  <div class="abs field" style="top:277px">Enter Your Text
    <span class="mic" style="right:5px;top:5px;width:20px;height:20px">
      <svg width="8" height="11" viewBox="0 0 8 11"><rect x="2.2" y="0.5" width="3.6" height="6" rx="1.8" fill="none" stroke="#fff"/><path d="M1 5a3 3 0 0 0 6 0M4 8v2.5" fill="none" stroke="#fff"/></svg>
    </span>
  </div>
  <div class="abs btn-gold btn-create">
    <svg class="btn-icon" width="14" height="16" viewBox="0 0 14 16"><circle cx="7" cy="4.5" r="3.5" fill="none" stroke="#2a1a10"/><path d="M1 15.5v-2a4 4 0 0 1 4-4h4a4 4 0 0 1 4 4v2z" fill="none" stroke="#2a1a10"/></svg>
    Create a Free account
  </div>
  <p class="abs tagline">Any Responsible Person can do it.</p>
  <div class="abs btn-login">
    <svg class="btn-icon" width="16" height="16" viewBox="0 0 16 16"><circle cx="8" cy="8" r="7" fill="none" stroke="#fff"/><path d="M3 8h8M8 5l3 3-3 3" fill="none" stroke="#fff"/></svg>
    Customer Log in
  </div>
  <svg class="abs finger" viewBox="0 0 38 41">
    <path d="M1 8V3a2 2 0 0 1 2-2h5M30 1h5a2 2 0 0 1 2 2v5M37 33v5a2 2 0 0 1-2 2h-5M8 40H3a2 2 0 0 1-2-2v-5" fill="none" stroke="#fff" stroke-width="1.2"/>
    <rect x="5" y="5" width="28" height="31" rx="4" fill="#fff"/>
    <path d="M13 26c0-8 2-13 6-13s6 5 6 13M16 28c0-7 1-11 3-11s3 4 3 11M19 20v10" fill="none" stroke="#777" stroke-width="1"/>
  </svg>
  <p class="abs credit">Created and endorsed by Serving Firefighters.</p>
</section>

<section class="screen screen--dashboard">
  <svg class="abs" style="left:0;top:0" width="254" height="110">
    <path d="M121 68l-10 14M133 68l10 14M90 92l-8 12M165 92l8 12" stroke="#e9c9c5" stroke-dasharray="2 2" fill="none"/>
  </svg>
  <div class="abs gauge">
    <svg width="34" height="34" viewBox="0 0 34 34"><path d="M7 20a10 10 0 0 1 20 0" fill="none" stroke="#e23" stroke-width="3"/><path d="M17 22l4-10" stroke="#222" stroke-width="1.5"/><circle cx="17" cy="22" r="2.5" fill="#222"/></svg>
  </div>
  <div class="abs plus"><svg width="16" height="16"><path d="M8 1v14M1 8h14" stroke="#fff" stroke-width="3"/></svg></div>
  <div class="abs start-box">Start Fire Risk Assessment</div>
  <div class="abs tile tile--commercial" role="img" aria-label="Photo of commercial office towers"></div>
  <div class="abs tile tile--residential" role="img" aria-label="Photo of a residential house"></div>
  <span class="abs tile-label" style="left:46px">Commercial</span>
  <span class="abs tile-label" style="left:135px">Residential</span>
  <div class="abs complete">Complete
    <svg class="tick" width="17" height="17"><circle cx="8.5" cy="8.5" r="8" fill="#fff"/><path d="M5 9l2.5 2.5L12 6.5" fill="none" stroke="#0bbf00" stroke-width="1.8"/></svg>
  </div>
  <div class="abs site-link">Reed's Barbershop
    <svg width="34" height="17" viewBox="0 0 34 17"><path d="M0 8.5h28M23 4.5l5 4-5 4" fill="none" stroke="#fff" stroke-width="1.2"/><circle cx="25.5" cy="8.5" r="7.5" fill="none" stroke="#fff"/></svg>
  </div>
  <div class="abs btn-gold section-bar" style="top:264px">In Progress</div>
  <div class="abs radio-row" style="top:300px"><span class="radio"></span>Elm Road School</div>
  <div class="abs radio-row" style="top:321px"><span class="radio radio--on"></span>Oakfield Care Home</div>
  <div class="abs btn-gold section-bar" style="top:350px">Purchases</div>
  <div class="abs radio-row" style="top:386px"><span class="radio radio--on"></span>Residential Fire Risk Assessment</div>
  <div class="abs radio-row" style="top:407px"><span class="radio"></span>Commercial Fire Risk Assessment</div>
  <div class="abs radio-row" style="top:429px"><span class="radio"></span>Commercial Fire Risk Assessment</div>
  <nav class="abs nav">
    <span class="nav-pill" style="left:1px;width:80px"></span>
    <div class="nav-item nav-item--active" style="left:44px"><svg width="16" height="16"><circle cx="8" cy="8" r="7.5" fill="#fff"/><path d="M3 10a5 5 0 0 1 10 0" fill="none" stroke="#e23" stroke-width="1.6"/><path d="M8 10l2-5" stroke="#222"/></svg>Blaze Check</div>
    <div class="nav-item" style="left:107px"><svg width="18" height="16"><rect x="1" y="4" width="16" height="10" rx="2" fill="#f2b52c"/><rect x="1" y="7" width="16" height="2" fill="#555"/><path d="M5 4l5-3 3 3" fill="#4a8fd8"/></svg>Purchases</div>
    <div class="nav-item" style="left:162px"><svg width="18" height="16"><rect x="1" y="1" width="11" height="8" rx="2" fill="#f2b52c"/><rect x="6" y="5" width="11" height="9" rx="2" fill="#f8cf3a" stroke="#5a3a10" stroke-width=".8"/><circle cx="11.5" cy="9.5" r="2" fill="none" stroke="#5a3a10" stroke-width=".8"/></svg>Support</div>
    <div class="nav-item" style="left:218px"><svg width="14" height="16"><rect x="1" y="1" width="12" height="14" rx="1" fill="#18a84a"/><path d="M5 4l2 3-2 4M7 7h3" stroke="#fff" fill="none"/></svg>Log Out</div>
  </nav>
</section>

<section class="screen screen--support">
  <svg class="abs support-icon" width="35" height="30" viewBox="0 0 35 30">
    <rect x="1" y="1" width="22" height="15" rx="3" fill="#f2b52c" stroke="#5a3a10" stroke-width=".8"/>
    <rect x="10" y="9" width="24" height="17" rx="3" fill="#f8cf3a" stroke="#5a3a10" stroke-width=".8"/>
    <circle cx="17" cy="17.5" r="3.5" fill="none" stroke="#5a3a10" stroke-width="1.2"/>
    <path d="M24 15h6M24 19h5" stroke="#5a3a10" stroke-width="1.2"/>
  </svg>
  <h2 class="abs support-title" style="font-weight:400">Technical Support</h2>
  <p class="abs prompt">Typr / record your response here.</p>
  <span class="mic" style="left:213px;top:78px;width:22px;height:22px;border:1.2px solid #fff">
    <svg width="8" height="11" viewBox="0 0 8 11"><rect x="2.2" y="0.5" width="3.6" height="6" rx="1.8" fill="none" stroke="#fff"/><path d="M1 5a3 3 0 0 0 6 0M4 8v2.5" fill="none" stroke="#fff"/></svg>
  </span>
  <div class="abs textbox">Kasle osejcsoe caseincs okseuncs kaseinc.</div>
  <div class="abs btn-gold btn-send">Send
    <svg width="15" height="14" viewBox="0 0 15 14"><path d="M1 6l13-5-5 12-2-5z M7 8l7-7" fill="none" stroke="#2a1a10"/></svg>
  </div>
  <nav class="abs nav">
    <span class="nav-pill" style="left:132px;width:61px;border-radius:24px 24px 24px 24px"></span>
    <div class="nav-item" style="left:44px"><svg width="16" height="16"><circle cx="8" cy="8" r="7.5" fill="#fff" stroke="#ccc"/><path d="M3 10a5 5 0 0 1 10 0" fill="none" stroke="#e23" stroke-width="1.6"/><path d="M8 10l2-5" stroke="#222"/></svg>Blaze Check</div>
    <div class="nav-item" style="left:107px"><svg width="18" height="16"><rect x="1" y="4" width="16" height="10" rx="2" fill="#f2b52c"/><rect x="1" y="7" width="16" height="2" fill="#555"/><path d="M5 4l5-3 3 3" fill="#4a8fd8"/></svg>Purchases</div>
    <div class="nav-item nav-item--active" style="left:162px"><svg width="18" height="16"><rect x="1" y="1" width="11" height="8" rx="2" fill="#f2b52c"/><rect x="6" y="5" width="11" height="9" rx="2" fill="#f8cf3a" stroke="#5a3a10" stroke-width=".8"/><circle cx="11.5" cy="9.5" r="2" fill="none" stroke="#5a3a10" stroke-width=".8"/></svg>Support</div>
    <div class="nav-item" style="left:218px"><svg width="14" height="16"><rect x="1" y="1" width="12" height="14" rx="1" fill="#18a84a"/><path d="M5 4l2 3-2 4M7 7h3" stroke="#fff" fill="none"/></svg>Log Out</div>
  </nav>
</section>

</body>
</html>
```